Clear Plastic Card Design

I am looking to have a business card designed from my logo icon. I am looking to match the style of a different business card I have attached in the files.
Looking for a card that is plastic, with layers of transparency in the shape of my logo icon (also attached in the files) - not a circle like the other card. The winning design will incorporate the red icon logo on the front and back and include the charity's name, "Light for the Weary Souls" in the same or similar font, as well as an email and phone number. For now, use the email: email@lightfortheweary-mail.org and the phone number 555-382-7194.
We like how the sample business card has transparency, partial and full opacity layers and a matching color scheme. Files will need to be in vector so that our business card printing company can work with it.
UPDATE:
We've some excellent designs in, thank you everyone! I got an early review from the owner, and he requested a minor redirect to find his perfect design. He wants the design to stand out by NOT being a rectangle. Try instead a circle, square, or best yet - something that falls in the outline of the logo icon, either fully or partially. Thank you, everyone!
Light for the Weary Souls text should be incorporated as well as a phone and email.

```html
<!DOCTYPE html>
<html lang="en">
<head>
<meta charset="utf-8">
<title>Light for the Weary Souls – Clear Card</title>
<link href="https://fonts.googleapis.com/css2?family=Poppins:wght@300;600;700&display=swap" rel="stylesheet">
<style>
  :root {
    --bg-top: #dcdddf;
    --bg-bottom: #ffffff;
    --card-front: rgba(240, 240, 242, 0.75);
    --card-back: rgba(255, 255, 255, 0.8);
    --edge-front: #e6bdb1;
    --edge-back: #f3b6a2;
    --ink: #939393;
    --ink-light: #a3a3a3;
    --accent: #e08f98;
    --tone-rose: #d88f9f;
    --tone-peach: #e9b08c;
  }
  html, body {
    margin: 0;
    padding: 0;
    width: 1200px;
    height: 1200px;
    overflow: hidden;
  }
  body {
    background: linear-gradient(180deg, var(--bg-top) 0%, #f1f1f2 50%, var(--bg-bottom) 78%);
    font-family: "Poppins", sans-serif;
  }
  .stage { display: block; width: 1200px; height: 1200px; }
  .card-front { fill: var(--card-front); stroke: var(--edge-front); stroke-width: 4; }
  .card-back { fill: var(--card-back); stroke: var(--edge-back); stroke-width: 5; }
  .brand-mark { opacity: 0.9; }
  .brand-name { font-family: "Poppins", sans-serif; font-weight: 700; font-size: 44px; fill: var(--accent); }
  .charity-name { font-family: "Poppins", sans-serif; font-weight: 700; font-size: 60px; fill: var(--ink); }
  .role-title { font-family: "Poppins", sans-serif; font-weight: 600; font-size: 40px; fill: var(--ink); }
  .contact-text { font-family: "Poppins", sans-serif; font-weight: 300; font-size: 24px; fill: var(--ink-light); }
  .icon-ring { fill: none; stroke: var(--accent); stroke-width: 2; }
  .icon-glyph { fill: var(--accent); }
</style>
</head>
<body>
<svg class="stage" viewBox="0 0 1920 1920" xmlns="http://www.w3.org/2000/svg">
  <defs>
    <linearGradient id="brandTone" x1="0" y1="1" x2="1" y2="0">
      <stop offset="0" stop-color="var(--tone-rose)"/>
      <stop offset="1" stop-color="var(--tone-peach)"/>
    </linearGradient>
    <path id="cardShape" d="M670 903 H1010 Q1040 903 1062 887 L1262 737 Q1290 715 1296 682 L1340 460 V205 Q1340 95 1230 95 H965 Q950 95 950 110 V160 H745 V415 L615 545 Q592 568 592 600 V823 Q592 903 670 903 Z"/>
  </defs>

  <!-- Front -->
  <g class="front">
    <use href="#cardShape" class="card-front"/>
    <g class="brand-lockup">
      <rect class="brand-mark" x="955" y="110" width="370" height="370" rx="10" fill="url(#brandTone)"/>
      <text class="brand-name" x="960" y="545">Light for the</text>
      <text class="brand-name" x="960" y="597">Weary Souls</text>
    </g>
    <text class="charity-name">
      <tspan x="655" y="627">Light</tspan>
      <tspan x="655" y="697">for the</tspan>
      <tspan x="655" y="767">Weary</tspan>
      <tspan x="655" y="837">Souls</tspan>
    </text>
  </g>

  <!-- Back -->
  <g class="back" transform="translate(0 912)">
    <use href="#cardShape" class="card-back"/>
    <g class="brand-lockup">
      <rect class="brand-mark" x="955" y="110" width="370" height="370" rx="10" fill="url(#brandTone)" opacity="0.75"/>
      <text class="brand-name" x="960" y="545">Light for the</text>
      <text class="brand-name" x="960" y="597">Weary Souls</text>
    </g>
    <text class="role-title">
      <tspan x="652" y="650">Marketing</tspan>
      <tspan x="652" y="696">Director</tspan>
    </text>
    <g class="contact-phone">
      <circle class="icon-ring" cx="668" cy="758" r="16"/>
      <path class="icon-glyph" d="M662 749 q3 -2 5 1 l2 4 q1 2 -1 3 l-1 1 q2 4 5 6 l1 -1 q1 -2 3 -1 l4 2 q3 2 1 5 q-3 4 -8 1 q-8 -5 -12 -13 q-2 -5 1 -8 z"/>
      <text class="contact-text" x="708" y="767">555-382-7194</text>
    </g>
    <g class="contact-email">
      <circle class="icon-ring" cx="668" cy="818" r="16"/>
      <rect class="icon-glyph" x="659" y="812" width="18" height="12" rx="1"/>
      <path d="M659 813 L668 820 L677 813" fill="none" stroke="#ffffff" stroke-width="1.5"/>
      <text class="contact-text" x="710" y="826">email@lightfortheweary-mail.org</text>
    </g>
  </g>
</svg>
</body>
</html>
```